Business Card Design Project

This is the first time we use our new logo. We need a business card that we can use both on our institutional corporate relationships and also that works for our staff that deals with consumers directly.

VELUNDA is a new company dedicated to empower consumers and to provide them with the best choices for specialized health care using the latest telemedicine technology (medicine at a distance via videoconference).

We want to print this cards in high quality materials and process. We will like designs that allow us to use UV spot varnish and other techniques that will differentiate us.

We are including Two different versions of Color logos. In addition we are including white over black background logos. Those can be used replacing the black for a color.

Please note this is the first time we will be creating any corporate materials with our new logo and colors.

Target Market(s)

34+ consumers of medium high and high socioeconomic levels.

Industry/Entity Type

Health

Requirements
Must have
• Our logo on its original colors
Should not have
• Any other graphical element or design that is not our logo

```html
<!DOCTYPE html>
<html lang="en">
<head>
<meta charset="utf-8">
<title>VELUNDA Business Card</title>
<link href="https://fonts.googleapis.com/css2?family=Montserrat:wght@400;600;700&display=swap" rel="stylesheet">
<style>
  :root {
    --navy: #1a5580;
    --sky: #58b4de;
    --teal: #1aa397;
    --paper: #ffffff;
    --ink: #222222;
    --backdrop: #eceff2;
  }
  html, body {
    margin: 0;
    padding: 0;
    width: 1200px;
    height: 1057px;
    overflow: hidden;
    background: var(--backdrop);
    font-family: "Montserrat", sans-serif;
  }
  .canvas {
    position: relative;
    width: 1200px;
    height: 1057px;
  }
  .card {
    position: absolute;
    width: 620px;
    height: 354px;
    overflow: hidden;
    box-shadow: 0 6px 18px rgba(0,0,0,0.18);
  }
  .card--front { left: 70px; top: 90px; background: var(--paper); }
  .card--back  { left: 510px; top: 600px; background: var(--sky); }

  .front-bands { position: absolute; inset: 0; }

  .brand {
    position: absolute;
    left: 48px;
    top: 112px;
    display: flex;
    align-items: center;
    gap: 18px;
  }
  .brand__dot {
    width: 44px;
    height: 44px;
    border-radius: 50%;
    background: var(--navy);
  }
  .brand__name {
    font-weight: 700;
    font-size: 46px;
    letter-spacing: 4px;
    color: var(--navy);
  }

  .person {
    position: absolute;
    left: 60px;
    top: 220px;
  }
  .person__name {
    font-weight: 700;
    font-size: 24px;
    color: var(--navy);
    margin: 0;
  }
  .person__title {
    font-size: 17px;
    color: var(--teal);
    margin: 2px 0 10px;
  }
  .person__address {
    font-size: 14px;
    line-height: 1.45;
    color: var(--ink);
    margin: 0;
    font-style: normal;
  }

  .contact {
    position: absolute;
    left: 440px;
    top: 104px;
    margin: 0;
    padding: 0;
    list-style: none;
    color: var(--paper);
    font-size: 14px;
    line-height: 1;
  }
  .contact li {
    display: flex;
    align-items: center;
    gap: 8px;
    margin-bottom: 12px;
  }
  .contact svg { width: 14px; height: 14px; flex: none; }

  .back-brand {
    position: absolute;
    left: 0;
    right: 0;
    top: 110px;
    display: flex;
    flex-direction: column;
    align-items: center;
    gap: 18px;
  }
  .back-brand__dot {
    width: 70px;
    height: 70px;
    border-radius: 50%;
    background: var(--paper);
  }
  .back-brand__name {
    font-weight: 700;
    font-size: 40px;
    letter-spacing: 6px;
    color: var(--paper);
  }
  .back-web {
    position: absolute;
    left: 0;
    right: 0;
    bottom: 42px;
    text-align: center;
    color: var(--paper);
    font-size: 20px;
    font-weight: 600;
    letter-spacing: 6px;
  }
</style>
</head>
<body>
<main class="canvas">

  <section class="card card--front" aria-label="Card front">
    <svg class="front-bands" viewBox="0 0 620 354" preserveAspectRatio="none" aria-hidden="true">
      <path d="M380 0 C430 90 400 230 250 354 L620 354 L620 0 Z" fill="var(--sky)"/>
      <path d="M420 0 C455 100 420 240 285 354 L620 354 L620 0 Z" fill="var(--navy)"/>
    </svg>

    <div class="brand">
      <span class="brand__dot"></span>
      <span class="brand__name">VELUNDA</span>
    </div>

    <div class="person">
      <h2 class="person__name">Your Name</h2>
      <div class="person__title">Title</div>
      <address class="person__address">Street Name, City Name<br>State, City Zip Code</address>
    </div>

    <ul class="contact">
      <li>
        <svg viewBox="0 0 16 16" aria-hidden="true"><circle cx="8" cy="8" r="7" fill="none" stroke="currentColor" stroke-width="1.5"/><path d="M5.5 4.5 L7 4.5 L7.5 6.5 L6.6 7.2 C7 8.3 7.7 9 8.8 9.4 L9.5 8.5 L11.5 9 L11.5 10.5 C8 10.8 5.2 8 5.5 4.5 Z" fill="currentColor"/></svg>
        012-555-0147
      </li>
      <li>
        <svg viewBox="0 0 16 16" aria-hidden="true"><circle cx="8" cy="8" r="7" fill="none" stroke="currentColor" stroke-width="1.5"/><path d="M5.5 4.5 L7 4.5 L7.5 6.5 L6.6 7.2 C7 8.3 7.7 9 8.8 9.4 L9.5 8.5 L11.5 9 L11.5 10.5 C8 10.8 5.2 8 5.5 4.5 Z" fill="currentColor"/></svg>
        012-555-0147
      </li>
      <li>
        <svg viewBox="0 0 16 16" aria-hidden="true"><rect x="1.5" y="3.5" width="13" height="9" fill="none" stroke="currentColor" stroke-width="1.5"/><path d="M1.5 3.5 L8 9 L14.5 3.5" fill="none" stroke="currentColor" stroke-width="1.5"/></svg>
        name@velunda.com
      </li>
      <li>
        <svg viewBox="0 0 16 16" aria-hidden="true"><circle cx="8" cy="8" r="6.5" fill="none" stroke="currentColor" stroke-width="1.3"/><ellipse cx="8" cy="8" rx="3" ry="6.5" fill="none" stroke="currentColor" stroke-width="1.1"/><path d="M1.5 8 H14.5" stroke="currentColor" stroke-width="1.1"/></svg>
        www.velunda.com
      </li>
    </ul>
  </section>

  <section class="card card--back" aria-label="Card back">
    <div class="back-brand">
      <span class="back-brand__dot"></span>
      <span class="back-brand__name">VELUNDA</span>
    </div>
    <div class="back-web">www.velunda.com</div>
  </section>

</main>
</body>
</html>
```